Letterhead, stationery and email signature for construction business

I need the letterhead, stationery and email signature designs for a construction business. I want them to have a corporate feel to them.

I've attached the logo for reference.

```html
<!DOCTYPE html>
<html lang="en">
<head>
<meta charset="utf-8">
<title>Halvern Projects Letterhead</title>
<link href="https://fonts.googleapis.com/css2?family=Lato:wght@400;700;900&family=Open+Sans:wght@400&family=Italianno&display=swap" rel="stylesheet">
<style>
  :root {
    --backdrop: #e4e4e4;
    --paper: #ffffff;
    --brand-blue: #2e55a0;
    --rule-blue: #2a6cc4;
    --slate: #6d7087;
    --ink: #1c1c1c;
  }
  * { box-sizing: border-box; margin: 0; padding: 0; }
  html, body { width: 1200px; height: 1141px; overflow: hidden; background: var(--backdrop); }
  .letterhead {
    position: absolute; left: 210px; top: 20px;
    width: 779px; height: 1101px;
    background: var(--paper);
    box-shadow: 0 2px 10px rgba(0,0,0,.18);
    overflow: hidden;
    font-family: "Lato", sans-serif; color: var(--ink);
  }
  .brand {
    position: absolute; left: 39px; top: 52px;
    display: flex; align-items: center; gap: 16px;
  }
  .brand-mark { width: 84px; height: 84px; background: var(--brand-blue); flex: none; }
  .brand-name {
    font-family: "Lato", sans-serif; font-weight: 900;
    color: var(--brand-blue); font-size: 46px; line-height: 1; letter-spacing: 1px;
  }
  .brand-name span { display: block; font-size: 24px; letter-spacing: 13.5px; margin-top: 6px; }
  .contact-rule {
    position: absolute; left: 511px; top: 46px; width: 2px; height: 111px; background: var(--rule-blue);
  }
  .contact {
    position: absolute; left: 539px; top: 41px; font-style: normal;
    font-family: "Open Sans", sans-serif; font-size: 16.5px; color: #2a2a2a; line-height: 22px;
  }
  .contact .address { margin-bottom: 8px; }
  .contact-line { display: flex; align-items: center; gap: 6px; }
  .contact-line svg { width: 13px; height: 13px; fill: var(--rule-blue); flex: none; }
  .letter-body {
    position: absolute; left: 39px; top: 250px; width: 701px;
    font-size: 15.7px; line-height: 17.4px;
  }
  .date { margin-bottom: 20px; line-height: 19px; font-size: 16px; }
  .recipient, .company { margin-bottom: 18px; font-size: 15.5px; line-height: 18.5px; }
  .salutation { font-weight: 700; font-size: 19.5px; margin: 10px 0 24px; }
  .letter-body p.copy { text-align: justify; margin-bottom: 17px; }
  .closing { margin-top: 38px; font-size: 16px; }
  .signature {
    font-family: "Italianno", cursive; font-size: 44px; margin-top: 88px; line-height: 1;
  }
  .footer-rule {
    position: absolute; left: 0; bottom: 120px; width: 100%; height: 6px; background: var(--slate);
  }
  .footer-band {
    position: absolute; left: 0; bottom: 0; width: 100%; height: 110px; background: var(--brand-blue);
  }
</style>
</head>
<body>
<main class="letterhead">
  <header>
    <div class="brand">
      <div class="brand-mark"></div>
      <div class="brand-name">HALVERN<span>PROJECTS</span></div>
    </div>
    <div class="contact-rule"></div>
    <address class="contact">
      <div class="address">Your address, City<br>State, Zip 1234</div>
      <div class="contact-line">
        <svg viewBox="0 0 16 16"><path d="M2 6c0-2 3-4 6-4s6 2 6 4l-3 1-1-2H6L5 7 2 6zM4 8h8l2 6H2z"/></svg>123 456 789</div>
      <div class="contact-line">
        <svg viewBox="0 0 16 16"><path d="M1 4h14v9H1zM1 4l7 5 7-5" stroke="#fff" stroke-width="1"/></svg>info@yourgmail.com</div>
      <div class="contact-line">
        <svg viewBox="0 0 16 16"><circle cx="8" cy="8" r="7"/><path d="M5 4c2 1 1 3 3 3s1 3 3 3M4 11c2-1 3 1 4 2" stroke="#fff" fill="none"/></svg>www.yourwebsite.com</div>
    </address>
  </header>

  <section class="letter-body">
    <div class="date">January-03-2020</div>
    <div class="recipient">Mr, Paul Grant<br>President</div>
    <div class="company">Brook Corporation<br>123 Street Name, Suite# 10<br>City, State, 120023</div>
    <div class="salutation">Dear Mr, Paul</div>
    <p class="copy">Lorem ipsum dolor sit amet, consectetur adipiscing elit, sed do eiusmod tempor incididunt ut labore et dolore magna aliqua. Ut enim ad minim veniam, quis nostrud exercitation ullamco laboris nisi ut aliquip ex ea commodo consequat. Duis aute irure dolor in reprehenderit in voluptate velit esse cillum dolore eu fugiat nulla pariatur.</p>
    <p class="copy">Lorem ipsum dolor sit amet, consectetur adipiscing elit, sed do eiusmod tempor incididunt ut labore et dolore magna aliqua. Ut enim ad minim veniam, quis nostrud exercitation ullamco laboris nisi ut aliquip ex ea commodo consequat. Duis aute irure dolor in reprehenderit in voluptate velit esse cillum dolore eu fugiat nulla pariatur.</p>
    <p class="copy">Lorem ipsum dolor sit amet, consectetur adipiscing elit, sed do eiusmod tempor incididunt ut labore et dolore magna aliqua. Ut enim ad minim veniam, quis nostrud exercitation ullamco laboris nisi ut aliquip ex ea commodo consequat.</p>
    <p class="copy">Excepteur sint occaecat cupidatat non proident, sunt in culpa qui officia deserunt mollit anim id est laborum. re et dolore magnam aliquam quaerat voluptatem.</p>
    <div class="closing">Regards</div>
    <div class="signature">Adrian Cole</div>
  </section>

  <footer>
    <div class="footer-rule"></div>
    <div class="footer-band"></div>
  </footer>
</main>
</body>
</html>
```